Corvane Paintless Dent Removal

Our company works on vehicles removing dents using a highly skilled trade which the metal is massaged out with special tools without disturbing the original paint, hence paintless dent removal. Besides keeping the paint and metal original its also very environmentally friendly since no paint or toxic fillers are used. Also we we are one of the most experienced companies in the business with 25 years

Target Market(s)

Retail Automobile consumers, Auto Dealerships and Auto Body Shops

Industry/Entity Type

Auto Repair

Contact Information for Business Card

Dale Hollister
PO Box 518 Brookmere, NY 11962
631-555-0148
corvanepdr@mailbox-example.com
website corvanepdr.example
youtube corvane paintless dent removal
25 years of experience removing Dents, Dings and Hail Damage

Font styles to use
Serif
Sans Serif

Colors

Designer to choose colors to be used in the design.

Requirements
Must have
• I do like things that are simple but classy and somewhat bold, also I like my logo so that should be somewhat important

```html
<!DOCTYPE html>
<html lang="en">
<head>
<meta charset="utf-8">
<title>Corvane Paintless Dent Removal – Business Card</title>
<link rel="stylesheet" href="https://fonts.googleapis.com/css2?family=Archivo:wght@400;700;800&family=Arimo:wght@400;700&display=swap">
<style>
  :root {
    --backdrop: #2b2d31;
    --lime: #72c11f;
    --forest: #2f7a34;
    --deep-navy: #0e3556;
    --navy: #1b3a5c;
    --white: #ffffff;
    --paper: #f6f6f6;
    --ink: #2a2a2a;
    --rule: #9a9a9a;
  }
  * { margin: 0; padding: 0; box-sizing: border-box; }
  html, body { width: 1200px; height: 864px; overflow: hidden; }
  body {
    background: var(--backdrop);
    font-family: "Arimo", Arial, sans-serif;
    position: relative;
  }
  .card {
    position: absolute;
    left: 300px;
    width: 600px;
    height: 343px;
    border-radius: 4px;
    overflow: hidden;
  }
  /* Front */
  .card--front {
    top: 69px;
    background: linear-gradient(135deg, var(--lime) 0%, var(--forest) 45%, var(--deep-navy) 100%);
    color: var(--white);
    text-align: center;
  }
  .brand {
    font-family: "Archivo", Arial, sans-serif;
    font-weight: 800;
    line-height: 1;
    letter-spacing: 0.5px;
  }
  .card--front .brand {
    margin-top: 58px;
    font-size: 34px;
    color: var(--white);
  }
  .card--front .brand span { display: block; font-size: 20px; margin-top: 6px; }
  .tagline {
    font-family: "Archivo", Arial, sans-serif;
    font-weight: 800;
    font-size: 17px;
    line-height: 1.2;
    margin-top: 42px;
    text-transform: uppercase;
  }
  .front-rule {
    width: 400px;
    height: 1px;
    background: rgba(255,255,255,0.55);
    margin: 22px auto 0;
  }
  .channel {
    display: flex;
    align-items: center;
    justify-content: center;
    gap: 10px;
    margin-top: 22px;
    font-size: 17px;
  }
  .channel .mark {
    width: 22px; height: 16px;
    background: var(--white);
    border-radius: 3px;
  }
  /* Back */
  .card--back {
    top: 452px;
    background: var(--paper);
    color: var(--ink);
  }
  .card--back .brand {
    position: absolute;
    top: 66px;
    right: 60px;
    font-size: 32px;
    color: var(--navy);
    text-align: center;
  }
  .card--back .brand span { display: block; font-size: 19px; margin-top: 5px; }
  .person {
    position: absolute;
    left: 38px;
    top: 170px;
    right: 36px;
    display: flex;
    align-items: center;
    gap: 6px;
  }
  .person__name {
    font-family: "Archivo", Arial, sans-serif;
    font-weight: 700;
    font-size: 21px;
    text-transform: uppercase;
    color: var(--navy);
    white-space: nowrap;
  }
  .person__name em { font-style: normal; color: var(--lime); }
  .person__rule { flex: 1; height: 1px; background: var(--rule); margin-top: 8px; }
  .contacts {
    position: absolute;
    left: 38px;
    top: 210px;
    list-style: none;
    font-size: 16px;
    line-height: 21px;
  }
  .contacts li { display: flex; align-items: center; gap: 6px; }
  .contacts svg { width: 12px; height: 12px; fill: var(--lime); }
  .address {
    position: absolute;
    right: 36px;
    bottom: 46px;
    text-align: right;
    font-size: 16px;
    line-height: 21px;
  }
</style>
</head>
<body>

<section class="card card--front">
  <div class="brand">Corvane<span>Paintless Dent Removal</span></div>
  <p class="tagline">25 Years of Experience Removing Dents<br>Dings and Hail Damage</p>
  <div class="front-rule"></div>
  <p class="channel"><span class="mark"></span>corvane paintless dent removal</p>
</section>

<section class="card card--back">
  <div class="brand">Corvane<span>Paintless Dent Removal</span></div>
  <div class="person">
    <span class="person__name">Dale <em>Hollister</em></span>
    <span class="person__rule"></span>
  </div>
  <ul class="contacts">
    <li>
      <svg viewBox="0 0 12 12" aria-hidden="true"><path d="M2 1h3l1 3-2 1c1 2 2 3 4 4l1-2 3 1v3c-6 0-10-4-10-10z"/></svg>
      631-555-0148
    </li>
    <li>
      <svg viewBox="0 0 12 12" aria-hidden="true"><path d="M0 2h12v8H0z M0 2l6 5 6-5" stroke="#f6f6f6" stroke-width="1"/></svg>
      corvanepdr@mailbox-example.com
    </li>
    <li>
      <svg viewBox="0 0 12 12" aria-hidden="true"><circle cx="6" cy="6" r="5.5"/></svg>
      corvanepdr.example
    </li>
  </ul>
  <p class="address">PO Box 518 Brookmere<br>NY 11962</p>
</section>

</body>
</html>
```